Jolly Hounds Dog Behaviour, Training and Natural Healthcare Business Card Design

I am an experienced and qualified dog behavioural trainer and natural animal healthcare consultant offering a range of services to help pet dog owners with the "whole dog".
COLOURS: A soft light blue in the background - can be fading out or split, red should also feature
LOGO: Dog, healing hands, silhouette, shadow
SERVICES: Behaviour Consults, Training, Complex Skills Coaching Walking Coaching, Diet & Nutrition, Environmental Enrichment, Lifestyle and Lifestage Adaptations, Massage, Natural Health Options
BY LINE: Happy Dogs, Happy Owners
VALUES: Promoting communication and connection between dogs and their owners.
FOCUS: Nutritional guidance and environmental adaptation are often needed to complete the package and increase the success rate of training and behaviour modification.

Target Market(s)

Everyone who has a dog who they wish to improve their relationship with

Industry/Entity Type

Communication

Contact Information for Business Card

Jolly Hounds, Rebecca Thornbury, 0427 861350, jollyhounds7@fernpost.example, www.jollyhounds7.example, Qualified Dog Behavioural Trainer and Natural Animal Healthcare Consultant

Font styles to use
Sans Serif
Script

Colors
85cae6
ec2027

Requirements
Must have
• A clear indication that it is a dog services business. A raised feature
Should not have
• Pawprints, cartoons

```html
<!DOCTYPE html>
<html lang="en">
<head>
<meta charset="utf-8">
<title>Jolly Hounds – Business Card</title>
<link rel="stylesheet" href="https://fonts.googleapis.com/css2?family=Merriweather:wght@700&family=Fira+Sans:wght@400&family=Fira+Sans+Condensed:wght@400&display=swap">
<style>
  :root {
    --stage: #2b2b2b;
    --card: #ffffff;
    --sky: #85cae6;
    --sky-soft: #d3ecf7;
    --red: #ec2027;
    --coat-light: #e9dcc4;
    --coat-mid: #b8915e;
    --coat-dark: #4a3626;
    --rug: #f1eeea;
  }
  html, body {
    margin: 0;
    width: 1200px;
    height: 900px;
    overflow: hidden;
    background: var(--stage);
  }
  .card {
    position: absolute;
    left: 100px;
    top: 150px;
    width: 1000px;
    height: 600px;
    background: linear-gradient(160deg, var(--card) 0%, var(--card) 38%, var(--sky-soft) 72%, var(--sky) 100%);
    overflow: hidden;
  }
  .card-art {
    position: absolute;
    inset: 0;
  }
  .brand-name {
    position: absolute;
    left: 430px;
    width: 460px;
    top: 66px;
    margin: 0;
    text-align: center;
    font-family: "Merriweather", Georgia, serif;
    font-weight: 700;
    font-size: 52px;
    line-height: 1;
    color: var(--red);
  }
  .credentials {
    position: absolute;
    left: 430px;
    top: 134px;
    width: 515px;
    margin: 0;
    font-family: "Fira Sans", Arial, sans-serif;
    font-size: 19px;
    line-height: 1.25;
    color: var(--red);
  }
  .credentials .line-one { display: block; padding-left: 110px; }
  .credentials .line-two { display: block; }
  .rule {
    position: absolute;
    left: 430px;
    top: 191px;
    width: 515px;
    height: 4px;
    background: var(--red);
  }
  .person-name {
    position: absolute;
    left: 475px;
    top: 208px;
    margin: 0;
    font-family: "Fira Sans Condensed", "Arial Narrow", sans-serif;
    font-size: 38px;
    color: var(--red);
  }
  .contact {
    position: absolute;
    left: 400px;
    width: 520px;
    top: 400px;
    margin: 0;
    padding: 0;
    list-style: none;
    text-align: center;
    font-family: "Fira Sans", Arial, sans-serif;
    font-size: 27px;
    line-height: 1.4;
    color: var(--red);
  }
</style>
</head>
<body>
  <article class="card">
    <svg class="card-art" width="1000" height="600" viewBox="0 0 1000 600">
      <defs>
        <linearGradient id="dogs-tones" x1="0" y1="0" x2="1" y2="1">
          <stop offset="0" stop-color="var(--rug)"/>
          <stop offset="0.3" stop-color="var(--coat-mid)"/>
          <stop offset="0.55" stop-color="var(--coat-dark)"/>
          <stop offset="0.75" stop-color="var(--coat-mid)"/>
          <stop offset="1" stop-color="var(--coat-light)"/>
        </linearGradient>
      </defs>
      <path class="dogs-photo" role="img" aria-label="Photo of two long-haired small dogs with bows in their topknots, sitting on a white rug"
            d="M0 0 L430 0 Q380 430 130 600 L0 600 Z" fill="url(#dogs-tones)"/>
      <path class="photo-edge" d="M430 0 Q380 430 130 600" fill="none" stroke="var(--red)" stroke-width="5"/>
    </svg>

    <h1 class="brand-name">Jolly Hounds</h1>
    <p class="credentials">
      <span class="line-one">Qualified Dog Behavioural</span>
      <span class="line-two">Trainer and Natural Animal Healthcare Consultant</span>
    </p>
    <div class="rule"></div>
    <p class="person-name">Rebecca Thornbury</p>

    <ul class="contact">
      <li class="phone">0427 861350</li>
      <li class="web">www.jollyhounds7.example</li>
      <li class="email">jollyhounds7@fernpost.example</li>
    </ul>
  </article>
</body>
</html>
```